Kestrelbrook Student Accomodation needs a business card design

Hi Guys,

We are a Student Accommodation company in Australia. We already have a logo which I will submit.

I will require the design of the business cards from you.

I am after something that looks clean, modern and that people feel interested and actually want to contact us.

We would like to see designs that are innovative.

On the business cards I will require to have:

Employee Name
Position
Phone number
Email
Facebook page

I hope you can help me with this project guys as I have heard really good things from you.

```html
<!DOCTYPE html>
<html lang="en">
<head>
<meta charset="UTF-8">
<title>Kestrelbrook Student Accomodation – Business Card</title>
<link rel="stylesheet" href="https://fonts.googleapis.com/css2?family=Open+Sans:wght@400;600;700&display=swap">
<style>
  :root {
    --bg: #e9e8e6;
    --card-white: #ffffff;
    --brand-green: #1f9a1f;
    --brand-yellow: #f2b312;
    --ink-dark: #1d3d1d;
    --shadow: rgba(0, 0, 0, 0.18);
  }
  * { margin: 0; padding: 0; box-sizing: border-box; }
  html, body {
    width: 1200px;
    height: 800px;
    overflow: hidden;
    background: var(--bg);
    font-family: "Open Sans", Arial, sans-serif;
  }
  .stage {
    position: relative;
    width: 1200px;
    height: 800px;
  }
  .card {
    position: absolute;
    background: var(--card-white);
    box-shadow: 0 6px 18px var(--shadow);
    overflow: hidden;
  }
  /* Front: horizontal card */
  .card-front {
    left: 155px;
    top: 245px;
    width: 540px;
    height: 310px;
  }
  .front-shape {
    position: absolute;
    inset: 0;
  }
  .contact-block {
    position: absolute;
    left: 30px;
    top: 26px;
    color: var(--ink-dark);
  }
  .person-name {
    font-size: 17px;
    font-weight: 600;
    letter-spacing: 0.5px;
    text-transform: uppercase;
  }
  .person-role {
    font-size: 12px;
    margin-top: 1px;
  }
  .address {
    font-size: 11.5px;
    line-height: 1.5;
    margin-top: 40px;
    margin-left: 22px;
  }
  .contact-list {
    list-style: none;
    margin-top: 40px;
    font-size: 12px;
  }
  .contact-list li {
    display: flex;
    align-items: center;
    gap: 9px;
    line-height: 1.85;
  }
  .contact-list svg {
    width: 12px;
    height: 12px;
    flex: none;
  }
  .brand-mark {
    position: absolute;
    display: flex;
    align-items: center;
    gap: 8px;
    font-weight: 700;
    color: var(--brand-green);
  }
  .brand-dot {
    background: var(--brand-yellow);
    border-radius: 50%;
    flex: none;
  }
  .card-front .brand-mark {
    left: 350px;
    top: 138px;
    font-size: 22px;
  }
  .card-front .brand-dot { width: 14px; height: 14px; }
  /* Back: vertical card */
  .card-back {
    left: 735px;
    top: 130px;
    width: 310px;
    height: 540px;
    background: linear-gradient(180deg, #ffffff 0%, #f3f3f3 100%);
  }
  .card-back .brand-mark {
    left: 50%;
    top: 50%;
    transform: translate(-50%, -50%);
    font-size: 28px;
  }
  .card-back .brand-dot { width: 18px; height: 18px; }
</style>
</head>
<body>
<main class="stage">

  <section class="card card-front" aria-label="Business card front">
    <svg class="front-shape" viewBox="0 0 540 310" preserveAspectRatio="none" aria-hidden="true">
      <path d="M0 0 H318 C250 50 230 190 262 310 H0 Z" fill="var(--brand-green)"/>
      <path d="M318 0 C250 50 230 190 262 310" fill="none" stroke="var(--brand-yellow)" stroke-width="16"/>
    </svg>

    <div class="contact-block">
      <p class="person-name">Liam Hartwell</p>
      <p class="person-role">Managing Director</p>
      <p class="address">112 4th Floor Arcade<br>Marlow Street NSW</p>
      <ul class="contact-list">
        <li>
          <svg viewBox="0 0 24 24" aria-hidden="true"><path fill="var(--ink-dark)" d="M6.6 10.8a15 15 0 0 0 6.6 6.6l2.2-2.2a1 1 0 0 1 1-.25 11.4 11.4 0 0 0 3.6.57 1 1 0 0 1 1 1V20a1 1 0 0 1-1 1A17 17 0 0 1 3 4a1 1 0 0 1 1-1h3.5a1 1 0 0 1 1 1c0 1.25.2 2.45.57 3.57a1 1 0 0 1-.25 1z"/></svg>
          <span>021 555 0147</span>
        </li>
        <li>
          <svg viewBox="0 0 24 24" aria-hidden="true"><rect x="2" y="5" width="20" height="14" rx="2" fill="none" stroke="var(--ink-dark)" stroke-width="2"/><path d="M3 6l9 7 9-7" fill="none" stroke="var(--ink-dark)" stroke-width="2"/></svg>
          <span>hello@kestrelbrook.au</span>
        </li>
        <li>
          <svg viewBox="0 0 24 24" aria-hidden="true"><circle cx="12" cy="12" r="10" fill="none" stroke="var(--ink-dark)" stroke-width="2"/><path d="M2 12h20M12 2c3 3 3 17 0 20M12 2c-3 3-3 17 0 20" fill="none" stroke="var(--ink-dark)" stroke-width="1.6"/></svg>
          <span>www.kestrelbrook.au</span>
        </li>
      </ul>
    </div>

    <div class="brand-mark">
      <span class="brand-dot"></span>
      <span class="brand-name">Kestrelbrook</span>
    </div>
  </section>

  <section class="card card-back" aria-label="Business card back">
    <div class="brand-mark">
      <span class="brand-dot"></span>
      <span class="brand-name">Kestrelbrook</span>
    </div>
  </section>

</main>
</body>
</html>
```